Calvanto Group Real Estate Company business cards

New business card design, we are generally happy with the basic layout of the existing front of business card, (feel free to change) but require a head shot photo on the back side.

http://www.calvanto.com.au/

Attached logos, and existing business card

------------------------------

Target Market(s)

Real estate

Industry/Entity Type

Real Estate

Contact Information for Business Card

Standard size double sided

Font styles to use
Other font styles liked:
• Futura

Requirements
Must have
• Photo head shot on the back side
Nice to have
• yes
Should not have
• No

```html
<!DOCTYPE html>
<html lang="en">
<head>
<meta charset="utf-8">
<title>Calvanto Group – Business Cards</title>
<link href="https://fonts.googleapis.com/css2?family=Open+Sans:wght@400;600;700&family=Roboto+Condensed:wght@600&display=swap" rel="stylesheet">
<style>
  :root {
    --purple: #2c1f6e;
    --orange: #f7941d;
    --ink: #4a4a4a;
    --card: #fafafa;
    --stage: #3a3a3a;
  }
  * { margin: 0; padding: 0; box-sizing: border-box; }
  html, body { width: 1200px; height: 750px; overflow: hidden; }
  body {
    background: var(--stage);
    font-family: "Open Sans", Arial, sans-serif;
    position: relative;
  }
  .card { position: absolute; background: var(--card); }

  /* Front */
  .card-front { left: 214px; top: 321px; width: 460px; height: 263px; }
  .brand { position: absolute; left: 20px; top: 110px; width: 196px; text-align: center; }
  .brand-name {
    font-size: 24px; font-weight: 600; color: var(--purple);
    letter-spacing: -0.3px; line-height: 1; white-space: nowrap;
  }
  .services {
    margin-top: 16px;
    font-family: "Roboto Condensed", Arial, sans-serif;
    font-weight: 600; font-size: 12px; color: var(--purple);
    word-spacing: 4px; line-height: 1;
  }
  .divider { position: absolute; left: 228px; top: 71px; width: 1px; height: 132px; background: #d6d6d6; }
  .contact { position: absolute; left: 248px; top: 67px; color: var(--ink); }
  .person-name { font-size: 17px; font-weight: 600; color: var(--purple); line-height: 1.2; }
  .person-role { font-size: 12.5px; color: var(--orange); line-height: 1.2; margin-bottom: 10px; }
  .company, .abn { font-size: 12px; line-height: 1.4; }
  .company { font-weight: 600; }
  .abn { margin-bottom: 5px; }
  .line { display: flex; align-items: center; gap: 6px; font-size: 12px; line-height: 1.5; white-space: nowrap; }
  .line svg { width: 11px; height: 11px; fill: var(--purple); flex: none; }
  .rule-orange { position: absolute; left: 0; top: 242px; width: 100%; height: 2px; background: var(--orange); }
  .band-purple { position: absolute; left: 0; top: 244px; width: 100%; height: 19px; background: var(--purple); }

  /* Back */
  .card-back { left: 705px; top: 130px; width: 263px; height: 461px; background: #fff; }
  .frame { position: absolute; left: 8px; top: 10px; width: 246px; height: 441px; border: 3px solid var(--purple); }
  .headshot {
    position: absolute; left: 0; top: 0; width: 100%; height: 332px;
    background: linear-gradient(180deg, #2e1f6c 0%, #2a1d63 70%, #263152 100%);
  }
  .back-brand { position: absolute; left: 0; top: 350px; width: 100%; text-align: center; }
  .back-brand .brand-name { font-size: 25px; }
  .back-brand .services { margin-top: 16px; }
  .web { margin-top: 10px; font-size: 11px; letter-spacing: 2.4px; color: var(--ink); white-space: nowrap; }
</style>
</head>
<body>

<section class="card card-front">
  <div class="brand">
    <div class="brand-name">Calvanto Group</div>
    <div class="services">Buy | Sell | Rent</div>
  </div>
  <div class="divider"></div>
  <div class="contact">
    <div class="person-name">Daniel Tran</div>
    <div class="person-role">Director</div>
    <div class="company">Calvanto Group</div>
    <div class="abn">ABN: 12 345 678 901</div>
    <div class="line">
      <svg viewBox="0 0 24 24"><path d="M6.6 10.8a15.1 15.1 0 0 0 6.6 6.6l2.2-2.2a1 1 0 0 1 1-.25 11.4 11.4 0 0 0 3.6.57 1 1 0 0 1 1 1V20a1 1 0 0 1-1 1A17 17 0 0 1 3 4a1 1 0 0 1 1-1h3.5a1 1 0 0 1 1 1c0 1.25.2 2.45.57 3.57a1 1 0 0 1-.25 1z"/></svg>
      <span>0412 555 019</span>
    </div>
    <div class="line">
      <svg viewBox="0 0 24 24"><path d="M2 5h20v14H2z M2 5l10 7 10-7" fill="none" stroke="#2c1f6e" stroke-width="2.5"/></svg>
      <span>daniel.tran@calvanto.com.au</span>
    </div>
    <div class="line">
      <svg viewBox="0 0 24 24"><circle cx="12" cy="12" r="10"/><path d="M2 12h20M12 2c3 3 3 17 0 20M12 2c-3 3-3 17 0 20" fill="none" stroke="#fff" stroke-width="1.5"/></svg>
      <span>www.calvanto.com.au</span>
    </div>
  </div>
  <div class="rule-orange"></div>
  <div class="band-purple"></div>
</section>

<section class="card card-back">
  <div class="frame">
    <div class="headshot" role="img" aria-label="Head shot photo of the director in a navy suit and blue tie against a purple backdrop"></div>
    <div class="back-brand">
      <div class="brand-name">Calvanto Group</div>
      <div class="services">Buy | Sell | Rent</div>
      <div class="web">www.calvanto.com.au</div>
    </div>
  </div>
</section>

</body>
</html>
```